Systems and Technology Consultants - Website

Design & Build a website for a new company which operates in the Systems and Technology space for Transportation, Government and Commercial sectors.

Overall design should be minimalist in nature.
Should also have a feed that provides news and event updates on the main page.
Logo has already been awarded and should be incorporated into the site.

We like the overall layout, functionality and simplicity of the below sites. Submitted designs could be similar to or a combination of the aspects on these sites, or perhaps a whole different concept - we are open to new ideas.
Norvique.com
Teblo.it

Update 1 Dated 27 May 2014

All I am moving away from the Teblo.it website and would like it to be more aligned with Norvique.com not only in layout but in functionality. I will be extending the deadline of this design brief for two weeks to incorporate additional requirements and will add addtional funding to the project.

Apologies for not having more information available to provide but with so many submissions its getting confusing.

Thanks Derek

Please note that the brief has been updated and the deadline has been extended.

Important: We will need two language versions of the website, English and Arabic; the website is hosted on HostPelican

Hello All, Thank you for your submissions. We have narrowed it down to the final 6 designers and I just wanted to take a moment and provide a bit of feedback regarding the concepts that we like and the modifications we are looking for. First, let me mention some of the design functions we like. - At the top of the homepage we really like the "region" or "language" tab so that the website can be viewed in both English and Arabic. - We like the homepage to have clear color variation so that the different sections of the homepage are distinct. Additionally, we like the bottom portion of the homepage to be in red. We feel that draws attention to our contact information. Again, we would like the colors to integrate black, gray-scale, red, etc. - Having a search tab at the top of the home page, or integrated into the main image, so that the site is easy to navigate. - We especially like the main image to have the scrolling tabs at the bottom so it is easy to browse the services offered (Consultancy, Solutions Architecture, Masters Systems Integration, Independent Design Review). - In regards to the services offered tab we really like the idea that a few people presented that have the outside of our logo with an icon in the middle of consultancy, solutions, etc., etc. Secondly, as mentioned in our brief we really enjoy the design of norvique site. Specially, we enjoy the strong iconic images they use, the way the tabs at the top scroll easily, and contact us page that generates an email. Lastly, I've included some photos of the concept we have been working on. What we are trying to demonstrate is how our company offers a range of services that are essentially linked together. We provide individual services that when combined present the full service package. We would like this concept to be integrated into the over concept of our website. Please feel free to ask for clarification of any of the above points or contact us if you have any additional questions. We appreciate all of your hard work and are very excited to see the updated designs. Best, Marta Vennick Quelbrant Senior Program Manager marta.vennick@quelbrant-example.com

Industry/Entity Type

Government

Font styles to use
Serif
Sans Serif

Requirements
Must have
• Must work on/adapt to various/mobile devices (responsive)
Must be simple and straightforward
Colors should be in line/matching with logo
2 language versions: English and Arabic (no Thai)
Services should be the first group/row of items after/below the main image
Note: the website will be hosted by hostpelican
Nice to have
• Submit feedback form
What's New section
The banner at the bottom of the site should not be too large; we would like a narrow one more
It would be nice if the header/top banner (with Home, About, etc. tabs) could stay in place as you scroll down (like Norvique and Chatterloop)
We will likely only use one image with a Company slogan on the Home page rather than a carousel of images to rotate through
Should not have
• This is the existing website: http://www.quelbrant-example.org
We do not like the animation, the way the banner icons/titles bounce
Not simple enough, we don't like the functionality or how pages load so slowly
We do not like the logo centered - it should be at the left
The banner and its tabs should not be towards the right, we would like them to be centered, to go all the way across and to be below the logo

```html
<!DOCTYPE html>
<html lang="en">
<head>
<meta charset="utf-8">
<title>Quelbrant International</title>
<link href="https://fonts.googleapis.com/css2?family=Open+Sans:wght@400;600&display=swap" rel="stylesheet">
<style>
:root{
  --red:#c8232b;
  --red-band:#c9474b;
  --ink:#333333;
  --text:#6a6a6a;
  --nav:#555555;
  --dark:#353535;
  --light:#f1f1f1;
  --line:#dedede;
  --footer:#333333;
  --footer-text:#bdbdbd;
  --white:#ffffff;
  --sky:#2fa6de;
  --amber:#f39c12;
  --coal:#1f1f1f;
}
*{margin:0;padding:0;box-sizing:border-box}
html,body{width:836px;height:1200px;overflow:hidden;background:var(--white)}
body{position:relative;font-family:"Open Sans",Arial,sans-serif;color:var(--text)}
.abs{position:absolute}

/* header */
.brand{left:70px;top:12px;width:96px;text-align:center;color:var(--red);font-weight:600}
.brand-mark{display:block;width:30px;height:30px;margin:0 auto 9px;background:var(--red)}
.brand-name{font-size:12px;letter-spacing:3px;line-height:14px}
.brand-sub{font-size:6px;letter-spacing:1.6px;line-height:8px}
.search{left:630px;top:18px;width:136px;height:29px;background:#f4f4f4;border:1px solid #dcdcdc;font-size:9px;color:#999;padding:7px 0 0 10px}
.search svg{position:absolute;right:6px;top:6px}
.main-nav{right:70px;top:67px;display:flex;gap:24px;list-style:none;font-size:10px;letter-spacing:.1px}
.main-nav li{color:var(--nav)}
.main-nav li.active{color:var(--red)}

/* slogan + hero */
.slogan{left:0;top:102px;width:836px;height:59px;background:var(--red-band);color:var(--white);font-size:15.5px;line-height:22px;text-align:center;padding-top:7px}
.hero{left:0;top:161px;width:836px;height:365px;
  background:
    radial-gradient(ellipse 170px 130px at 420px 70px,rgba(236,160,110,.85),rgba(236,160,110,0) 100%),
    radial-gradient(ellipse 260px 160px at 200px 110px,rgba(160,200,225,.55),rgba(160,200,225,0) 100%),
    radial-gradient(ellipse 200px 160px at 720px 120px,rgba(225,232,238,.8),rgba(225,232,238,0) 100%),
    radial-gradient(ellipse 520px 120px at 420px 330px,rgba(70,82,96,.55),rgba(70,82,96,0) 100%),
    linear-gradient(180deg,#4f6476 0%,#7d92a3 45%,#b9c5cf 80%,#e9edf0 100%)}
.arrow{top:284px;width:45px;height:58px;background:rgba(80,80,80,.75);display:flex;align-items:center;justify-content:center}
.arrow.prev{left:0}.arrow.next{right:0}

/* service tabs */
.services{left:69px;top:500px;width:698px;height:81px;display:flex;list-style:none}
.services li{background:var(--dark);color:var(--white);font-size:12px;text-align:center;padding-top:16px;border-right:1px solid #262626;letter-spacing:.2px}
.services li:last-child{border-right:0}
.services li.active{background:var(--red)}
.services svg{display:block;margin:0 auto 9px;height:22px}

/* welcome */
.welcome{left:71px;top:607px;width:518px}
.welcome h1{font-size:18.5px;font-weight:400;color:var(--red);margin-bottom:7px}
.welcome p{font-size:9.4px;line-height:16px;margin-bottom:6px}
.sectors{left:599px;top:612px;width:167px;height:159px;background:var(--light);list-style:none;padding:10px 0 0 12px}
.sectors li{font-size:11.4px;color:var(--red);line-height:24.8px}
.sectors li::before{content:"•";font-size:8px;margin-right:7px;vertical-align:1px}
.divider{left:69px;top:806px;width:698px;height:1px;background:var(--line)}

/* feeds */
.feed-title{top:832px;font-size:15px;font-weight:400}
.feed-title.news{left:72px;color:var(--red)}
.feed-title.events{left:432px;color:var(--ink)}
.more{top:836px;width:11px;height:11px;border-radius:50%;background:#c4c4c4}
.card{top:860px;width:160px}
.card .photo{width:160px;height:94px}
.card h3{font-size:11px;font-weight:400;line-height:16px;margin-top:8px}
.card.news h3{color:var(--red)}
.card.events h3{color:var(--ink)}
.card time{display:block;font-size:9.3px;color:var(--ink);margin-top:3px}
.card p{font-size:8.4px;line-height:13px;margin-top:6px}

/* footer */
.footer{left:0;top:1098px;width:836px;height:102px;background:var(--footer)}
.footer-nav{left:0;top:1117px;width:836px;display:flex;justify-content:center;gap:43px;list-style:none;font-size:10px;color:var(--footer-text)}
.footer-nav li::before{content:"• ";font-size:7px}
.footer-rule{left:69px;top:1147px;width:698px;height:1px;background:#474747}
.copyright{left:71px;top:1165px;font-size:10px;color:var(--footer-text)}
.social{top:1161px;width:24px;height:24px;border-radius:50%;border:2px solid #4a4a4a}
.social.one{left:678px;background:var(--sky)}
.social.two{left:710px;background:var(--coal)}
.social.three{left:741px;background:var(--amber)}
</style>
</head>
<body>

<header>
  <div class="abs brand">
    <span class="brand-mark"></span>
    <div class="brand-name">QUELBRANT</div>
    <div class="brand-sub">INTERNATIONAL</div>
  </div>
  <div class="abs search">Search
    <svg width="16" height="16" viewBox="0 0 16 16"><circle cx="6.5" cy="6.5" r="4.5" fill="none" stroke="#888" stroke-width="2"/><line x1="10" y1="10" x2="14" y2="14" stroke="#888" stroke-width="2.5"/></svg>
  </div>
  <ul class="abs main-nav">
    <li class="active">HOME</li><li>BUSINESS UNITS</li><li>SERVICES</li><li>ABOUT US</li><li>LOCATIONS</li><li>CONTACT US</li>
  </ul>
</header>

<div class="abs slogan">Quelbrant specializes in delivering quality professional services and technical<br>projects that support larger business goals.</div>

<div class="abs hero" role="img" aria-label="Business team in a meeting room looking at a glowing world map with network connections"></div>
<div class="abs arrow prev"><svg width="18" height="36" viewBox="0 0 18 36"><polyline points="16,2 2,18 16,34" fill="none" stroke="#fff" stroke-width="1.5"/></svg></div>
<div class="abs arrow next"><svg width="18" height="36" viewBox="0 0 18 36"><polyline points="2,2 16,18 2,34" fill="none" stroke="#fff" stroke-width="1.5"/></svg></div>

<ul class="abs services">
  <li class="active" style="width:132px">
    <svg viewBox="0 0 24 22" width="24"><circle cx="8" cy="7" r="4" fill="#fff"/><circle cx="16" cy="7" r="4" fill="#fff"/><path d="M1 20c0-5 3-7 7-7s7 2 7 7zM12 13.5c1-.4 2.5-.5 4-.5 4 0 7 2 7 7h-7" fill="#fff"/></svg>CONSULTING</li>
  <li style="width:145px">
    <svg viewBox="0 0 22 22" width="22"><path d="M3 1h5v15h13v5H3z" fill="#fff"/></svg>ENGINEERING</li>
  <li style="width:145px">
    <svg viewBox="0 0 22 22" width="22"><rect x="2" y="8" width="8" height="14" fill="#fff"/><rect x="11" y="1" width="9" height="21" fill="#fff"/><g fill="#353535"><rect x="13" y="4" width="2" height="2"/><rect x="16" y="4" width="2" height="2"/><rect x="13" y="9" width="2" height="2"/><rect x="16" y="9" width="2" height="2"/><rect x="13" y="14" width="2" height="2"/><rect x="16" y="14" width="2" height="2"/><rect x="4" y="11" width="2" height="2"/><rect x="4" y="16" width="2" height="2"/></g></svg>CONSTRUCTION</li>
  <li style="width:145px">
    <svg viewBox="0 0 22 22" width="22"><circle cx="9" cy="9" r="5" fill="none" stroke="#fff" stroke-width="3" stroke-dasharray="3 1.5"/><circle cx="17" cy="17" r="3" fill="none" stroke="#fff" stroke-width="2.2" stroke-dasharray="2 1"/></svg>OPERATIONS</li>
  <li style="width:131px">
    <svg viewBox="0 0 22 22" width="22"><line x1="3" y1="19" x2="19" y2="3" stroke="#fff" stroke-width="3"/><line x1="3" y1="3" x2="19" y2="19" stroke="#fff" stroke-width="3"/><circle cx="4" cy="4" r="3" fill="#fff"/></svg>MAINTENANCE</li>
</ul>

<section class="abs welcome">
  <h1>Welcome to Quelbrant International</h1>
  <p>Systems are tools that support a greater business function and need. we understand that most technical projects are conceptualized to support a larger vision with actual business goals in mind and ensure that all of our professional and certified expertise is included in our professional services to meet those goals. quelbrant recognizes the middle east and greater asia regions are economic growth markets with developing infrastructure projects requiring special­ist systems and technical expertise.&nbsp; accordingly, quelbrant has evolved its presence in the regions to meet client demands and expectations.</p>
  <p>Our ultimate goal is to provide quality, technical and professional services on projects of any scale and/or complexity, from conception through to completion.&nbsp; our philosophy is simple; stick to what you are good at and be the best at it.</p>
</section>
<ul class="abs sectors">
  <li>Telecommunications</li><li>Airports</li><li>Water treatment plants</li><li>Rail</li><li>Oil and gas</li><li>Ports</li>
</ul>
<div class="abs divider"></div>

<h2 class="abs feed-title news">Latest News</h2>
<span class="abs more" style="left:393px"></span>
<h2 class="abs feed-title events">Latest Events</h2>
<span class="abs more" style="left:753px"></span>

<article class="abs card news" style="left:72px">
  <div class="photo" role="img" aria-label="Business people shaking hands over a meeting table" style="background:linear-gradient(135deg,#5e5e5e,#a9a9a9 55%,#e3e3e3)"></div>
  <h3>Quis autem vel eum iure reprehenderit</h3><time>May 14, 2014</time>
  <p>Nemo enim ipsam voluptatem quia voluptas sit aspernatur aut odit aut fugit, sed quia consequuntur magni dolores eos qui ratione.</p>
</article>
<article class="abs card news" style="left:244px">
  <div class="photo" role="img" aria-label="Team working together at an office table" style="background:linear-gradient(135deg,#8a9aa6,#d4dbe0 55%,#6f7a84)"></div>
  <h3>Quis autem vel eum iure reprehenderit</h3><time>May 14, 2014</time>
  <p>Nemo enim ipsam voluptatem quia voluptas sit aspernatur aut odit aut fugit, sed quia consequuntur magni dolores eos qui ratione.</p>
</article>
<article class="abs card events" style="left:432px">
  <div class="photo" role="img" aria-label="Colleagues talking in a bright office beside a laptop" style="background:linear-gradient(135deg,#f2f2f2,#d9d9d9 60%,#9a9a9a)"></div>
  <h3>Quis autem vel eum iure reprehenderit</h3><time>May 14, 2014</time>
  <p>Nemo enim ipsam voluptatem quia voluptas sit aspernatur aut odit aut fugit, sed quia consequuntur magni dolores eos qui ratione.</p>
</article>
<article class="abs card events" style="left:604px">
  <div class="photo" role="img" aria-label="Travellers walking through a blue-lit transit concourse" style="background:linear-gradient(135deg,#2f9fd0,#8fd3f0 55%,#1f6f9c)"></div>
  <h3>Quis autem vel eum iure reprehenderit</h3><time>May 14, 2014</time>
  <p>Nemo enim ipsam voluptatem quia voluptas sit aspernatur aut odit aut fugit, sed quia consequuntur magni dolores eos qui ratione.</p>
</article>

<footer>
  <div class="abs footer"></div>
  <ul class="abs footer-nav">
    <li>Home</li><li>Business Units</li><li>Services</li><li>About us</li><li>Locations</li><li>Contact us</li>
  </ul>
  <div class="abs footer-rule"></div>
  <p class="abs copyright">Copyright &nbsp;©&nbsp; 2014 &nbsp; Quelbrant International. &nbsp; All rights reserved.</p>
  <span class="abs social one" role="img" aria-label="Social profile link"></span>
  <span class="abs social two" role="img" aria-label="Social profile link"></span>
  <span class="abs social three" role="img" aria-label="News feed link"></span>
</footer>

</body>
</html>
```